Valderons Business Card

Business card for philanthropic organization

Industry/Entity Type

Business

Contact Information for Business Card

Need a very ELEGANT, sober, embossed, formal business card... it should transmit CREDIBILITY. Not looking for a "fun card". would like white, grays or black designs.

Font styles to use
Script

Requirements
Must have
• Embossed look

```html
<!DOCTYPE html>
<html lang="en">
<head>
<meta charset="utf-8">
<title>Valderons Business Card</title>
<link rel="stylesheet" href="https://fonts.googleapis.com/css2?family=Andika&family=Italianno&display=swap">
<style>
  :root {
    --stage: #d9d7d3;
    --card-top: #ffffff;
    --card-bottom: #e9e9e9;
    --ink: #2b2b2b;
    --ink-soft: #4a4a4a;
    --rule: #3a3a3a;
    --emboss-light: rgba(255,255,255,0.95);
    --emboss-dark: rgba(0,0,0,0.18);
  }
  html, body {
    margin: 0;
    width: 1200px;
    height: 1023px;
    overflow: hidden;
    background: var(--stage);
  }
  .business-card {
    position: absolute;
    left: 100px;
    top: 226px;
    width: 1000px;
    height: 571px;
    border-radius: 22px;
    background: linear-gradient(160deg, var(--card-top) 0%, #f7f7f7 55%, var(--card-bottom) 100%);
    box-shadow: 0 2px 0 #cfcfcf, 0 4px 0 #e0e0e0, 0 6px 0 #c9c9c9, 0 18px 40px rgba(0,0,0,0.28);
    font-family: "Andika", sans-serif;
    color: var(--ink);
  }
  .embossed {
    text-shadow: -1px -1px 0 var(--emboss-light), 1px 1px 1px var(--emboss-dark);
  }
  .card-header {
    position: absolute;
    left: 56px;
    top: 44px;
    font-size: 30px;
    letter-spacing: 0.5px;
    color: var(--ink-soft);
    white-space: nowrap;
  }
  .card-header .holder { margin-right: 22px; }
  .brand-mark {
    position: absolute;
    left: 150px;
    top: 330px;
    display: flex;
    align-items: center;
    gap: 14px;
    font-size: 38px;
    color: var(--ink);
  }
  .brand-mark .dot {
    width: 22px;
    height: 22px;
    border-radius: 50%;
    background: var(--ink-soft);
    box-shadow: -1px -1px 0 var(--emboss-light), 1px 1px 2px var(--emboss-dark);
  }
  .divider {
    position: absolute;
    left: 548px;
    top: 210px;
    width: 1px;
    height: 280px;
    background: var(--rule);
    box-shadow: 1px 1px 0 var(--emboss-light);
  }
  .contact-block {
    position: absolute;
    left: 590px;
    top: 170px;
  }
  .contact-name {
    font-family: "Italianno", cursive;
    font-size: 92px;
    line-height: 0.9;
    margin: 0;
    font-weight: 400;
  }
  .contact-role {
    font-family: "Italianno", cursive;
    font-size: 30px;
    margin: 0 0 18px 30px;
    color: var(--ink-soft);
  }
  .contact-lines {
    list-style: none;
    margin: 0;
    padding: 0;
    font-size: 28px;
    line-height: 1.35;
  }
  .contact-lines li { display: flex; align-items: center; gap: 10px; }
  .contact-lines svg { width: 20px; height: 20px; flex: none; }
</style>
</head>
<body>
  <section class="business-card">
    <div class="card-header embossed">
      <span class="holder">Mateo Lindqvar</span><span class="title">Al Naseem Valderons Potentate 2017</span>
    </div>

    <div class="brand-mark embossed" aria-label="Valderons">
      <span class="dot"></span><span>Valderons</span>
    </div>

    <div class="divider"></div>

    <div class="contact-block embossed">
      <h1 class="contact-name">Devin Marsh</h1>
      <p class="contact-role">Director</p>
      <ul class="contact-lines">
        <li>P.O. Box 0712-04518</li>
        <li>Panama, Republic of Panama</li>
        <li>
          <svg viewBox="0 0 20 20" aria-hidden="true"><path d="M5 2 L8 6 L6.5 8 Q8 12 12 13.5 L14 12 L18 15 L16 18 Q6 18 2 6 Z" fill="none" stroke="#2b2b2b" stroke-width="1.6" stroke-linejoin="round"/></svg>
          +(507)-6210-4487
        </li>
        <li>
          <svg viewBox="0 0 20 20" aria-hidden="true"><rect x="2" y="4" width="16" height="12" fill="none" stroke="#2b2b2b" stroke-width="1.6"/><path d="M2 4 L10 11 L18 4" fill="none" stroke="#2b2b2b" stroke-width="1.6"/></svg>
          mlindqvar@mail.com
        </li>
      </ul>
    </div>
  </section>
</body>
</html>
```